Business Cards Design for the electrical wholesaler: clean bold dynamic :)

We need a business card design that would follow our latest brand guidelines. As an electrical wholesaler we want to bring a fresh look and feel into the industry. The design should be clean bold and dynamic. It should come alive with the renewed energy of our green colour. Our grey colour should keep things balanced and complement the notion of maturity and responsibility. We employ Lato as a corporate font however are not bound by this font and we’re open to interpretation here.

Target Market(s)

Electrical contractors

Industry/Entity Type

Business

Contact Information for Business Card

Logo
Name & Surname: Halyna Dorosh
Job Title: Director of Marketing
Email: halya.dorosh@quillmail.example
Cell phone: XXX.XXX.XXXX
Address: 20517 - 87 Ave. Edmonton, AB, Canada. T6K 4N8
Business Phone: 780.555.0184
Website: www.brovix.example

Font styles to use
Other font styles liked:
• Lato

Requirements
Must have
• Logo & website
Nice to have
• Brand elements - some of them you may find in the attached Brand Guidelines (e.g. three lines on the background signifying "W")

```html
<!DOCTYPE html>
<html lang="en">
<head>
<meta charset="utf-8">
<title>brovix business card</title>
<link rel="stylesheet" href="https://fonts.googleapis.com/css2?family=Work+Sans:wght@400;500&display=swap">
<style>
  :root {
    --page: #e9e6e1;
    --green: #7cb43c;
    --grey: #46484a;
    --ink: #f2f4ee;
    --ink-soft: rgba(242, 244, 238, 0.85);
    --edge: #d9dccf;
  }
  * { box-sizing: border-box; margin: 0; padding: 0; }
  html, body {
    width: 1200px;
    height: 1047px;
    overflow: hidden;
    background: var(--page);
    font-family: "Work Sans", "Lato", sans-serif;
  }
  .card {
    position: absolute;
    left: 100px;
    top: 251px;
    width: 1000px;
    height: 545px;
    border-radius: 20px;
    background: var(--green);
    overflow: hidden;
    box-shadow: 0 0 0 3px var(--edge);
    color: var(--ink);
  }
  .brand-panel {
    position: absolute;
    left: 485px;
    top: -4px;
    width: 540px;
    height: 553px;
    background: var(--grey);
    border-radius: 140px 0 0 140px;
    box-shadow: 0 0 0 6px var(--edge);
  }
  .brand {
    position: absolute;
    left: 57px;
    top: 44px;
    display: flex;
    align-items: center;
    gap: 14px;
  }
  .brand-dot {
    width: 40px;
    height: 40px;
    border-radius: 50%;
    background: var(--ink);
  }
  .brand-name {
    font-size: 52px;
    font-weight: 400;
    line-height: 1;
    letter-spacing: 1px;
    color: var(--ink);
  }
  .person {
    position: absolute;
    left: 54px;
    top: 244px;
  }
  .person-name {
    font-size: 33px;
    font-weight: 500;
    letter-spacing: 0.5px;
    color: var(--ink);
  }
  .person-title {
    margin-top: 4px;
    font-size: 21px;
    font-weight: 400;
    letter-spacing: 1px;
    color: var(--ink-soft);
  }
  .address {
    position: absolute;
    left: 54px;
    top: 326px;
    font-size: 20px;
    line-height: 32px;
    letter-spacing: 1px;
    color: var(--ink-soft);
  }
  .contacts {
    position: absolute;
    left: 54px;
    top: 402px;
    list-style: none;
    font-size: 20px;
    line-height: 31px;
    letter-spacing: 1px;
    color: var(--ink-soft);
  }
  .contacts li {
    display: flex;
    align-items: center;
    gap: 14px;
  }
  .contacts svg {
    width: 15px;
    height: 15px;
    fill: none;
    stroke: var(--ink-soft);
    stroke-width: 1.8;
  }
</style>
</head>
<body>
  <div class="card">
    <div class="brand-panel"></div>

    <div class="brand">
      <span class="brand-dot"></span>
      <span class="brand-name">brovix</span>
    </div>

    <div class="person">
      <p class="person-name">Halyna Dorosh</p>
      <p class="person-title">Founder</p>
    </div>

    <p class="address">20517 - 87 Ave.<br>Edmonton, AB, Canada. T6K 4N8</p>

    <ul class="contacts">
      <li>
        <svg viewBox="0 0 16 16" aria-hidden="true"><path d="M4 1.5 6.5 4.5 5 6.5c1 2 2.5 3.5 4.5 4.5l2-1.5 3 2.5-1.5 2.5C8 14 2 8 1.5 3z"/></svg>
        <span>780.555.0184</span>
      </li>
      <li>
        <svg viewBox="0 0 16 16" aria-hidden="true"><rect x="1.5" y="3.5" width="13" height="9" rx="1"/><path d="M1.5 4 8 9l6.5-5"/></svg>
        <span>halya.dorosh@quillmail.example</span>
      </li>
      <li>
        <svg viewBox="0 0 16 16" aria-hidden="true"><circle cx="8" cy="8" r="6.5"/><ellipse cx="8" cy="8" rx="3" ry="6.5"/><path d="M1.5 8h13"/></svg>
        <span>www.brovix.example</span>
      </li>
    </ul>
  </div>
</body>
</html>
```